New Business Card Design Project

We require a business card design for Vexalund, a newly established Indian company.
Our focus is on the development, manufacturing, and export of a diverse array of pharmaceutical products on a global scale. The card should convey a professional appearance, as our primary markets are in Africa, China, and Southeast Asian nations.
We envision a two-sided business card, with the reverse side dedicated to a logo set against a solid color or an elegantly designed pattern. The corners should be rounded. We would appreciate seeing both horizontal and vertical design options. We trust the designer to utilize their expertise in creating this design.

The content for the business card is included in the attached Word file.

Target Market(s)

Our primary markets are in Africa, China, and Southeast Asian, Latin America, Maldives, Sri Lanka

Industry/Entity Type

Pharmaceutical Manufacturing and Export

Contact Information for Business Card

Colors

Designer to choose colors to be used in the design.

Requirements
Must have
• The reverse side of the business card features solely the logo along with the tagline, "Remedies of Life."
Should not have
• The logo should not exceed two instances, encompassing both the front and back sides of the card.

```html
<!DOCTYPE html>
<html lang="en">
<head>
<meta charset="UTF-8">
<title>Vexalund Business Card</title>
<link href="https://fonts.googleapis.com/css2?family=Montserrat:wght@400;500;700;800&display=swap" rel="stylesheet">
<style>
  :root {
    --backdrop: #d9d8d4;
    --card-white: #ffffff;
    --brand-blue: #27a9e1;
    --brand-coral: #f0604d;
    --ink: #1e1e1e;
  }
  * { margin: 0; padding: 0; box-sizing: border-box; }
  html, body { width: 1200px; height: 801px; overflow: hidden; }
  body {
    background: var(--backdrop);
    font-family: "Montserrat", sans-serif;
    position: relative;
  }
  .card {
    position: absolute;
    top: 240px;
    width: 560px;
    height: 320px;
    border-radius: 16px;
    overflow: hidden;
    box-shadow: 0 14px 30px rgba(0,0,0,0.22);
  }
  .card-front { left: 26px; background: var(--card-white); }
  .card-back { left: 614px; background: var(--brand-coral); }

  .front-wave { position: absolute; inset: 0; width: 100%; height: 100%; }

  .brand-block {
    position: absolute;
    left: 30px;
    top: 104px;
    width: 220px;
    display: flex;
    align-items: center;
    gap: 10px;
  }
  .brand-dot {
    width: 20px; height: 20px; border-radius: 50%;
    background: var(--brand-blue);
    flex: none;
  }
  .brand-name {
    font-weight: 800;
    font-size: 34px;
    color: var(--brand-blue);
    letter-spacing: 0.5px;
  }

  .divider {
    position: absolute;
    left: 262px;
    top: 26px;
    width: 1px;
    height: 170px;
    background: var(--brand-blue);
  }

  .contact-block {
    position: absolute;
    left: 282px;
    top: 22px;
    width: 260px;
    color: var(--ink);
  }
  .person-name {
    font-weight: 800;
    font-size: 20px;
    color: var(--brand-blue);
    line-height: 1.2;
  }
  .person-role, .person-company {
    font-size: 13px;
    line-height: 1.35;
  }
  .contact-list { list-style: none; margin-top: 10px; }
  .contact-list li {
    display: flex; align-items: center; gap: 7px;
    font-size: 12px; line-height: 1.6;
  }
  .contact-icon { width: 12px; height: 12px; flex: none; }
  .address {
    margin-top: 10px;
    font-size: 12px;
    line-height: 1.45;
  }

  .back-brand {
    position: absolute;
    inset: 0;
    display: flex;
    flex-direction: column;
    align-items: center;
    justify-content: center;
    gap: 8px;
  }
  .back-name-row {
    display: flex;
    align-items: center;
    gap: 14px;
  }
  .back-dot {
    width: 28px; height: 28px; border-radius: 50%;
    background: var(--card-white);
  }
  .back-name {
    font-weight: 800;
    font-size: 58px;
    color: var(--card-white);
    letter-spacing: 1px;
    line-height: 1.1;
  }
  .tagline {
    font-weight: 500;
    font-size: 16px;
    color: var(--card-white);
    letter-spacing: 3px;
    text-transform: uppercase;
  }
</style>
</head>
<body>

  <section class="card card-front">
    <svg class="front-wave" viewBox="0 0 560 320" preserveAspectRatio="none" aria-hidden="true">
      <path d="M0 292 C 160 286, 250 262, 330 248 C 420 232, 480 232, 560 224 L560 320 L0 320 Z" fill="var(--brand-coral)"/>
      <path d="M0 299 C 162 293, 254 270, 334 256 C 424 240, 484 240, 560 232 L560 320 L0 320 Z" fill="var(--card-white)"/>
      <path d="M0 304 C 164 298, 258 276, 338 262 C 428 246, 488 246, 560 238 L560 320 L0 320 Z" fill="var(--brand-blue)"/>
    </svg>

    <div class="brand-block">
      <span class="brand-dot"></span>
      <span class="brand-name">Vexalund</span>
    </div>

    <div class="divider"></div>

    <div class="contact-block">
      <p class="person-name">Arjun K. Malvade</p>
      <p class="person-role">CEO</p>
      <p class="person-company">Vexalund</p>
      <ul class="contact-list">
        <li>
          <svg class="contact-icon" viewBox="0 0 12 12"><path d="M2.5 1 L4.5 1 L5.3 3.6 L4 4.6 C4.6 6 6 7.4 7.4 8 L8.4 6.7 L11 7.5 L11 9.5 C11 10.4 10.3 11 9.4 11 C5 10.6 1.4 7 1 2.6 C1 1.7 1.6 1 2.5 1 Z" fill="var(--brand-blue)"/></svg>
          +919812345670
        </li>
        <li>
          <svg class="contact-icon" viewBox="0 0 12 12"><rect x="0.5" y="2" width="11" height="8" rx="1" fill="var(--brand-coral)"/><path d="M1 2.5 L6 6.5 L11 2.5" stroke="#fff" stroke-width="1" fill="none"/></svg>
          amalvade@vexalund.com
        </li>
        <li>
          <svg class="contact-icon" viewBox="0 0 12 12"><circle cx="6" cy="6" r="5.3" fill="var(--brand-blue)"/><path d="M0.8 6 H11.2 M6 0.8 C3.5 3.5 3.5 8.5 6 11.2 M6 0.8 C8.5 3.5 8.5 8.5 6 11.2" stroke="#fff" stroke-width="0.8" fill="none"/></svg>
          www.vexalund.com
        </li>
      </ul>
      <p class="address">14, Kamal Vihar,<br>Sundarpur, 441120, India</p>
    </div>
  </section>

  <section class="card card-back">
    <div class="back-brand">
      <div class="back-name-row">
        <span class="back-dot"></span>
        <span class="back-name">Vexalund</span>
      </div>
      <p class="tagline">Remedies of Life</p>
    </div>
  </section>

</body>
</html>
```